Veltrane Group Business Card Design

The CEO is looking for a new trendy look for his business card.
You can stay with current branding or come up with something new/creative. It can be 3D, including Medical Office buildings. You can use our logo in a variety of colors. Please include name, title, company name, company website, email address, cell number

Target Market(s)

Real Estate Development and Construction

Industry/Entity Type

Health care real estate

Contact Information for Business Card

Rohesh Kamdar, CEO M-604.781.2249 E-roheshkamdar@veltrane.com Address:4180 Lindqvist Ave, Tampa, FL 33482 www.veltrane.com

Font styles to use
Other font styles liked:
• Be creative

Requirements
Must have
• Creative, trendy look
Nice to have
• Please go to our website to get a feel- www. veltrane.com
Should not have
• small fonts

```html
<!DOCTYPE html>
<html lang="en">
<head>
<meta charset="utf-8">
<title>Veltrane Group – Business Card</title>
<link href="https://fonts.googleapis.com/css2?family=Poppins:wght@800&family=Roboto+Slab:wght@400;500&display=swap" rel="stylesheet">
<style>
  :root {
    --backdrop: #3b3b3d;
    --card-black: #1a1a1b;
    --brand-red: #b01f29;
    --white: #ffffff;
    --emboss-grey: #5a5a5c;
  }
  * { box-sizing: border-box; margin: 0; padding: 0; }
  html, body { width: 1200px; height: 689px; overflow: hidden; }
  body {
    background: var(--backdrop);
    display: flex;
    align-items: center;
    justify-content: center;
    gap: 40px;
  }
  .card {
    position: relative;
    width: 540px;
    height: 308px;
    background: var(--card-black);
    overflow: hidden;
    box-shadow: 0 14px 34px rgba(0,0,0,.45);
  }
  .wordmark {
    font-family: "Poppins", sans-serif;
    font-weight: 800;
    letter-spacing: -1px;
    line-height: 1;
    white-space: nowrap;
  }
  .card-back .wordmark {
    position: absolute;
    left: 50%; top: 50%;
    transform: translate(-50%, -50%);
    font-size: 50px;
    color: var(--emboss-grey);
  }
  .card-front .red-panel {
    position: absolute;
    inset: 0;
    width: 100%;
    height: 100%;
  }
  .card-front .wordmark {
    position: absolute;
    left: 30px;
    top: 200px;
    font-size: 30px;
    color: var(--brand-red);
  }
  .details {
    position: absolute;
    left: 262px;
    top: 34px;
    color: var(--white);
  }
  .person-name {
    font-family: "Poppins", sans-serif;
    font-weight: 800;
    font-size: 25px;
    letter-spacing: .5px;
    line-height: 1.1;
  }
  .person-title {
    font-family: "Roboto Slab", serif;
    font-size: 14px;
    margin-top: 4px;
  }
  .contact-list {
    list-style: none;
    margin-top: 28px;
    font-family: "Roboto Slab", serif;
    font-size: 12.5px;
    line-height: 1.45;
  }
  .contact-list li {
    display: flex;
    align-items: flex-start;
    gap: 10px;
    margin-bottom: 5px;
  }
  .contact-list svg {
    width: 13px; height: 13px;
    flex: none;
    margin-top: 3px;
    fill: none;
    stroke: var(--white);
    stroke-width: 1.8;
  }
</style>
</head>
<body>

  <section class="card card-back" aria-label="Card back">
    <div class="wordmark">Veltrane Group</div>
  </section>

  <section class="card card-front" aria-label="Card front">
    <svg class="red-panel" viewBox="0 0 540 308" preserveAspectRatio="none" aria-hidden="true">
      <polygon points="205,0 540,0 540,308 268,308 246,146 252,118 218,96" fill="var(--brand-red)"/>
    </svg>

    <div class="wordmark">Veltrane Group</div>

    <div class="details">
      <div class="person-name">ROHESH KAMDAR</div>
      <div class="person-title">President / CEO</div>

      <ul class="contact-list">
        <li>
          <svg viewBox="0 0 14 14"><path d="M7 13s-4.5-4.6-4.5-7.7a4.5 4.5 0 0 1 9 0C11.5 8.4 7 13 7 13z"/><circle cx="7" cy="5.4" r="1.5"/></svg>
          <span>4180 Lindqvist Ave<br>Tampa, FL 33482</span>
        </li>
        <li>
          <svg viewBox="0 0 14 14"><rect x="3.5" y="1" width="7" height="12" rx="1.2"/><line x1="6" y1="11" x2="8" y2="11"/></svg>
          <span>604.781.2249</span>
        </li>
        <li>
          <svg viewBox="0 0 14 14"><rect x="1" y="3" width="12" height="8.5" rx="1"/><polyline points="1,3 7,8 13,3"/></svg>
          <span>roheshkamdar@veltrane.com</span>
        </li>
        <li>
          <svg viewBox="0 0 14 14"><circle cx="7" cy="7" r="5.8"/><ellipse cx="7" cy="7" rx="2.5" ry="5.8"/><line x1="1.2" y1="7" x2="12.8" y2="7"/></svg>
          <span>www.veltrane.com</span>
        </li>
      </ul>
    </div>
  </section>

</body>
</html>
```